White Paper and One-Page Advertisement for TELVORISH-QM

I need both documents to be better formatted and designed so they look professional, not something someone with mediocre word skills put together. They will go out to 1000s of industry professionals, and they need to look sharp. I need them to have my company's color palate logo, and branding on it similar to how it is now, but better. Please do not change any of the written content, but it can be arranged in any other format you think is better. Smart art and things i've already used can be omitted in favor of better designs. The developer is free to use their creativity. White paper should not be longer than the three pages unless necessary.

Target Market(s)

Life Sciences supply chain professionals

Colors
33b8a4
0592cd
9bcb3c
fbee3e
3277b5

Requirements
Must have
• Must be professional looking and not look like something done in word. Please use the color palate as seen on the documents.
Should not have
• Any changes to the written content.

```html
<!DOCTYPE html>
<html lang="en">
<head>
<meta charset="UTF-8">
<title>TELVORISH-QM — One-Page Advertisement</title>
<link href="https://fonts.googleapis.com/css2?family=Poppins:wght@400&family=Roboto+Condensed:wght@500&family=Roboto:wght@900&display=swap" rel="stylesheet">
<style>
  :root{
    --teal:#33b8a4;
    --sky:#0592cd;
    --lime:#9bcb3c;
    --sun:#fbee3e;
    --blue:#3277b5;
    --brand-green:#1f8a5e;
    --ink:#333a40;
    --white:#ffffff;
  }
  *{margin:0;padding:0;box-sizing:border-box}
  html,body{width:907px;height:1200px;overflow:hidden;background:var(--white)}
  .flyer{position:relative;width:907px;height:1200px;background:var(--white);font-family:"Poppins",sans-serif;color:var(--ink)}

  .masthead{position:absolute;top:0;left:0;width:100%;height:127px;display:flex;flex-direction:column;align-items:center;justify-content:center;gap:8px}
  .brand-dot{width:52px;height:52px;border-radius:50%;background:var(--lime)}
  .brand-name{font-family:"Roboto",sans-serif;font-weight:900;font-size:24px;letter-spacing:1px;color:var(--brand-green)}

  .hero{position:absolute;top:127px;left:0;width:100%;height:295px;
    background:linear-gradient(100deg,#b0873a 0%,#e8dccb 30%,#d9c6a8 45%,#3f6f78 70%,#2d5a63 100%)}
  .hero-rule{position:absolute;top:422px;left:0;width:100%;height:8px;background:var(--lime)}

  .section{position:absolute;left:0;width:100%}
  .section-tag{display:inline-block;margin-left:64px;width:226px;height:36px;border-radius:3px;
    font-family:"Roboto Condensed",sans-serif;font-weight:500;font-size:24px;line-height:36px;color:var(--white);padding-left:18px}
  .section-tag--platform{background:var(--blue)}
  .section-tag--benefits{background:var(--teal)}
  .section-tag--promise{background:var(--lime)}

  .checklist{list-style:none;margin-top:19px}
  .checklist li{position:relative;padding-left:64px;padding-right:44px;font-size:14.5px;line-height:20px;margin-bottom:17.5px}
  .checklist li svg{position:absolute;left:29px;top:4px;width:13px;height:13px}

  .platform{top:448px}
  .benefits{top:723px}
  .promise{top:1008px}

  .contact-bar{position:absolute;left:0;bottom:0;width:100%;height:74px;background:var(--blue);
    display:flex;align-items:center;justify-content:center;gap:50px;color:var(--white);font-size:16px}
  .contact-item{display:flex;align-items:center;gap:10px}
  .contact-item svg{width:13px;height:13px}
</style>
</head>
<body>
<div class="flyer">
  <svg width="0" height="0" style="position:absolute">
    <symbol id="tick-box" viewBox="0 0 13 13">
      <rect x="0.75" y="2.25" width="10" height="10" fill="none" stroke="#333a40" stroke-width="1.3"/>
      <path d="M3 6.5 L5.6 9.2 L12.3 1.2" fill="none" stroke="#333a40" stroke-width="1.6"/>
    </symbol>
  </svg>

  <header class="masthead">
    <span class="brand-dot"></span>
    <span class="brand-name">TELVORISH-QM</span>
  </header>

  <div class="hero" role="img" aria-label="Photograph of people smiling together at a traditional ceremony"></div>
  <div class="hero-rule"></div>

  <section class="section platform">
    <h2 class="section-tag section-tag--platform">OUR PLATFORM</h2>
    <ul class="checklist">
      <li><svg><use href="#tick-box"/></svg>A multi-vendor marketplace for the life science community to transact pre-market and after-market materials and equipment</li>
      <li><svg><use href="#tick-box"/></svg>Researchers, manufactures, and original suppliers can create an account to buy, sell, or donate materials</li>
      <li><svg><use href="#tick-box"/></svg>Part 11 compliant signature and authentication</li>
      <li><svg><use href="#tick-box"/></svg>Leverages industry auditing skills to facilitate compliant and transparent transactions</li>
      <li><svg><use href="#tick-box"/></svg>Some of the best and industry vendors and software used</li>
    </ul>
  </section>

  <section class="section benefits">
    <h2 class="section-tag section-tag--benefits">BENEFITS</h2>
    <ul class="checklist">
      <li><svg><use href="#tick-box"/></svg>Reduce write-offs by selling excess and obsolete materials, equipment, spare parts, etc.</li>
      <li><svg><use href="#tick-box"/></svg>Buy quality materials at a reduced price.</li>
      <li><svg><use href="#tick-box"/></svg>Market materials if an original supplier</li>
      <li><svg><use href="#tick-box"/></svg>Donate material to researchers</li>
      <li><svg><use href="#tick-box"/></svg>Acquire donated materials</li>
      <li><svg><use href="#tick-box"/></svg>Collaborate and consort to reduce supply chain risk such as mutual aid agreements, joint supplier audits, etc.</li>
    </ul>
  </section>

  <section class="section promise">
    <h2 class="section-tag section-tag--promise">OUR PROMISE</h2>
    <ul class="checklist">
      <li><svg><use href="#tick-box"/></svg>A greener, more cost-efficient, and quality driven supply chain through a collaborative life sciences marketplace.</li>
    </ul>
  </section>

  <footer class="contact-bar">
    <span class="contact-item">
      <svg viewBox="0 0 13 13"><rect x="0.5" y="2.5" width="12" height="8" fill="none" stroke="#fff"/><path d="M0.5 2.5 L6.5 7 L12.5 2.5" fill="none" stroke="#fff"/></svg>
      info@telvorishqm.com
    </span>
    <span class="contact-item">
      <svg viewBox="0 0 13 13"><path d="M6.5 12.5 C3 8 2.5 6.5 2.5 5 A4 4 0 0 1 10.5 5 C10.5 6.5 10 8 6.5 12.5Z" fill="#fff"/><circle cx="6.5" cy="5" r="1.5" fill="#3277b5"/></svg>
      www.telvorishqm.com
    </span>
    <span class="contact-item">
      <svg viewBox="0 0 13 13"><path d="M0.5 2.5 H5.5 Q6.5 2.5 6.5 3.5 V11 Q6.5 10 5.5 10 H0.5Z M12.5 2.5 H7.5 Q6.5 2.5 6.5 3.5 V11 Q6.5 10 7.5 10 H12.5Z" fill="none" stroke="#fff"/></svg>
      white paper
    </span>
  </footer>
</div>
</body>
</html>
```